Redesign of business card for Cedar Ridge Mechanical

We are looking for a new design for our business cards for Cedar Ridge Mechanical. We are a plumbing & HVAC construction company, operating on the West Coast of Canada and USA. Logo attached.
Industry/Entity Type
Construction - Plumbing & HVAC
Contact Information for Business Card
Name, address, phone numbers, email, website address
Look and feel
Each slider illustrates characteristics of the customer's brand and the style your logo design should communicate.

```html
<!DOCTYPE html>
<html lang="en">
<head>
<meta charset="utf-8">
<title>Cedar Ridge Mechanical – Business Card</title>
<link rel="stylesheet" href="https://fonts.googleapis.com/css2?family=Montserrat:wght@400;500;700&display=swap">
<style>
  :root {
    --backdrop: #7d6a52;
    --card-front: #ffffff;
    --card-back: #222222;
    --ink: #1f1f1f;
    --ink-soft: #2b2b2b;
    --back-mark: #0e0e0e;
  }
  * { margin: 0; padding: 0; box-sizing: border-box; }
  html, body { width: 900px; height: 1200px; overflow: hidden; }
  body {
    position: relative;
    background: var(--backdrop);
    font-family: "Montserrat", sans-serif;
    color: var(--ink);
  }
  .card {
    position: absolute;
    left: 80px;
    width: 742px;
    height: 440px;
    border-radius: 22px;
  }
  .card--front { top: 131px; background: var(--card-front); }
  .card--back { top: 638px; background: var(--card-back); }

  .brand-name {
    position: absolute;
    left: 120px;
    top: 176px;
    width: 210px;
    font-weight: 700;
    font-size: 25px;
    line-height: 1.2;
    text-transform: uppercase;
    color: var(--ink);
    text-align: center;
  }
  .divider {
    position: absolute;
    left: 356px;
    top: 156px;
    width: 2px;
    height: 147px;
    background: var(--ink);
  }
  .contact { position: absolute; left: 374px; top: 150px; }
  .contact__name { font-size: 25px; font-weight: 700; line-height: 1.2; color: var(--ink); }
  .contact__title { font-size: 15.5px; font-weight: 500; margin-top: 2px; color: var(--ink-soft); }
  .contact__list { list-style: none; margin-top: 20px; }
  .contact__item {
    display: flex;
    align-items: center;
    gap: 10px;
    font-size: 15.5px;
    font-weight: 500;
    height: 30.5px;
    color: var(--ink-soft);
  }
  .contact__icon { width: 16px; height: 16px; flex: none; fill: var(--ink); }
  .address {
    position: absolute;
    left: 0; right: 0;
    top: 374px;
    text-align: center;
    font-size: 15.5px;
    font-weight: 500;
    color: var(--ink-soft);
  }
  .back-mark {
    position: absolute;
    left: 0; right: 0;
    top: 170px;
    text-align: center;
    font-weight: 700;
    font-size: 44px;
    line-height: 1.15;
    text-transform: uppercase;
    color: var(--back-mark);
  }
</style>
</head>
<body>
  <section class="card card--front" aria-label="Business card front">
    <div class="brand-name">Cedar Ridge Mechanical</div>
    <div class="divider"></div>
    <div class="contact">
      <h1 class="contact__name">Daniel Reyes</h1>
      <p class="contact__title">Managing Director</p>
      <ul class="contact__list">
        <li class="contact__item">
          <svg class="contact__icon" viewBox="0 0 24 24" aria-hidden="true"><path d="M6.6 10.8a15.1 15.1 0 0 0 6.6 6.6l2.2-2.2a1 1 0 0 1 1-.25 11.4 11.4 0 0 0 3.6.57 1 1 0 0 1 1 1V20a1 1 0 0 1-1 1A17 17 0 0 1 3 4a1 1 0 0 1 1-1h3.5a1 1 0 0 1 1 1c0 1.25.2 2.45.57 3.57a1 1 0 0 1-.25 1z"/></svg>
          555.014.2290
        </li>
        <li class="contact__item">
          <svg class="contact__icon" viewBox="0 0 24 24" aria-hidden="true"><path d="M3 6h18v12H3z M3 6l9 6 9-6" fill="none" stroke="#1f1f1f" stroke-width="2"/><path d="M3 6h18l-9 6z"/></svg>
          info@cedarridgemechanical.com
        </li>
        <li class="contact__item">
          <svg class="contact__icon" viewBox="0 0 24 24" aria-hidden="true"><circle cx="12" cy="12" r="9" fill="none" stroke="#1f1f1f" stroke-width="2"/><path d="M3 12h18M12 3c3 3 3 15 0 18M12 3c-3 3-3 15 0 18" fill="none" stroke="#1f1f1f" stroke-width="1.6"/></svg>
          www.cedarridgemechanical.com
        </li>
      </ul>
    </div>
    <p class="address">27 Harbor View Lane Salem, OR 97301</p>
  </section>

  <section class="card card--back" aria-label="Business card back">
    <div class="back-mark">Cedar Ridge<br>Mechanical</div>
  </section>
</body>
</html>
```